Timber Ridge Athletics Web Design

Need to completely update website - simple and clean look - informative
this will be our main source for booking appointments etc. needs to have baseball and softball content. we currently have a site - looking to update - we would like you to design and add to our current site.

Target Market(s)

ages 15-45, youth and parents for kids- softball and baseball players /fitness

Industry/Entity Type

baseball and softball indoor training facility

Coding

Coded - Design and coding required

Number of Pages Required

5+ page

Colors

Designer to choose colors to be used in the design.

Requirements
Must have
• our colors of business are green and black- we need you to completely set up the website for us
Nice to have
• out current webiste is www.timberridge482.example

```html
<!DOCTYPE html>
<html lang="en">
<head>
<meta charset="utf-8">
<title>Timber Ridge Athletics – Baseball &amp; Softball Indoor Training</title>
<link href="https://fonts.googleapis.com/css2?family=Poppins:wght@400;500;600;700;800&display=swap" rel="stylesheet">
<style>
:root{
  --green:#4ff02c;
  --green-deep:#3fbf2a;
  --black:#111111;
  --nav:#161616;
  --footer:#2a2a2a;
  --card:#f1f1f1;
  --text:#333333;
  --white:#ffffff;
}
*{margin:0;padding:0;box-sizing:border-box}
html,body{width:1200px;height:3627px;overflow:hidden}
body{position:relative;font-family:'Poppins',sans-serif;background:var(--white);color:var(--text)}
.abs{position:absolute}
.btn{position:absolute;display:flex;align-items:center;justify-content:center;background:var(--green);color:var(--black);font-weight:700;border-radius:40px;text-transform:uppercase;font-size:17px;letter-spacing:.2px}
.brand{display:flex;align-items:center;gap:12px;font-weight:700}
.brand .dot{border-radius:50%;background:var(--green);border:3px solid var(--black)}

/* header */
.header{left:0;top:0;width:1200px;height:96px;background:var(--white)}
.header .brand{position:absolute;left:75px;top:18px;height:60px;font-size:24px;color:var(--black)}
.header .brand .dot{width:60px;height:60px}
.login{font-size:15px;height:46px;top:24px}
.nav{left:0;top:96px;width:1200px;height:57px;background:var(--nav);display:flex;align-items:center;padding-left:74px;gap:30px}
.nav a{color:var(--white);font-weight:600;font-size:16px;text-decoration:none}

/* hero */
.hero{left:0;top:153px;width:1200px;height:585px;background:linear-gradient(180deg,#3a4a57 0%,#6b6a5e 45%,#4d6b35 85%,#5c7a3a 100%)}
.hero-title{left:0;top:300px;width:1200px;text-align:center;color:var(--white);font-weight:800;font-size:104px;line-height:1;letter-spacing:2px}
.hero-sub{left:0;top:412px;width:1200px;text-align:center;color:var(--white);font-weight:700;font-size:30px}

/* about */
.about-title{left:75px;top:908px;font-size:40px;font-weight:800;color:var(--black)}
.about-text{left:75px;top:975px;width:480px;font-size:17px;line-height:34px;color:#444}
.about-frame{left:728px;top:853px;width:398px;height:362px;background:var(--green)}
.about-photo{left:587px;top:890px;width:508px;height:442px;background:linear-gradient(135deg,#c9564f 0%,#a8a092 40%,#5d7a45 70%,#b6825a 100%)}

/* facility */
.facility-bg{left:0;top:1415px;width:1200px;height:446px;background:linear-gradient(90deg,#3a2722,#5a3b33 40%,#2e3440 100%)}
.section-title-light{left:0;top:1470px;width:1200px;text-align:center;color:var(--white);font-size:40px;font-weight:700}
.card{top:1556px;width:512px;height:567px;background:var(--card)}
.card-photo{width:512px;height:305px}
.card h3{position:absolute;top:352px;width:100%;text-align:center;font-size:27px;font-weight:700;color:var(--black)}
.card p{position:absolute;top:402px;left:30px;right:30px;text-align:center;font-size:17px;line-height:34px;color:#444}

/* lessons */
.lessons-dark{left:0;top:2234px;width:1200px;height:479px;background:linear-gradient(90deg,#2a2a2a,#4a3a3a)}
.lesson-l{left:75px;top:2364px;color:var(--white);font-size:38px;font-weight:700;line-height:46px}
.lesson-l .price{color:var(--green)}
.lesson-r{right:74px;top:2340px;text-align:right;color:var(--white);font-size:38px;font-weight:700;line-height:46px}
.lessons-circle{left:469px;top:2340px;width:268px;height:268px;border-radius:50%;background:var(--white);border:5px solid var(--green);display:flex;align-items:center;justify-content:center;text-align:center;font-size:42px;font-weight:700;line-height:46px;color:var(--black)}

/* camps */
.camps-title{left:0;top:2768px;width:1200px;text-align:center;font-size:42px;font-weight:800;color:var(--black)}
.camp{top:2851px;width:338px;height:244px}

/* footer */
.site-footer{color:var(--white)}
.footer-bg{left:0;top:3196px;width:1200px;height:431px;background:var(--footer)}
.site-footer .brand{position:absolute;left:75px;top:3318px;font-size:18px;color:var(--white)}
.site-footer .brand .dot{width:52px;height:52px;border-color:var(--white)}
.copy{left:75px;top:3392px;font-size:14px;line-height:26px;color:var(--white)}
.social{top:3455px;width:28px;height:28px;border-radius:50%;background:var(--white)}
.foot-h{top:3262px;font-size:20px;font-weight:700;color:var(--white)}
.sitemap{left:355px;top:3302px;list-style:none;font-size:15px;line-height:35px;color:var(--white)}
.contact-row{left:596px;font-size:15px;line-height:22px;display:flex;gap:14px;color:var(--white)}
.contact-row svg{flex:none;margin-top:3px}
.hours{left:901px;top:3307px;font-size:15px;color:var(--white)}
.hours div{display:flex;height:42px}
.hours span:first-child{width:100px}
</style>
</head>
<body>

<header class="abs header">
  <div class="brand"><span class="dot"></span><span>Timber Ridge Athletics</span></div>
  <a class="btn login" style="left:822px;width:147px">Staff Login</a>
  <a class="btn login" style="left:979px;width:147px">Client Login</a>
</header>
<nav class="abs nav">
  <a>Home</a><a>About Us</a><a>Our Facility</a><a>Lessons</a><a>Team Rental Pricing</a><a>Instructor Opprtotunities</a><a>Camps/Classes</a><a>More</a>
</nav>

<section>
  <div class="abs hero" role="img" aria-label="Stadium scene with baseball players batting, catching and pitching under floodlights"></div>
  <h1 class="abs hero-title">TIMBER RIDGE</h1>
  <p class="abs hero-sub">BASEBALL &amp; SOFTBALL INDOOR TRAINING</p>
  <a class="btn" style="left:466px;top:476px;width:268px;height:48px;font-size:15px">Book Appointment</a>
  <svg class="abs" style="left:0;top:738px" width="600" height="80"><polygon points="0,0 592,0 0,79" fill="var(--green)"/></svg>
</section>

<section>
  <h2 class="abs about-title">WHO ARE WE?</h2>
  <p class="abs about-text">Timber Ridge Athletics is an elite baseball and softball training facility in Sacramento. We are committed to the development of these young athletes physically, mentally and emotionally on and off the field. We are here to train, guide and mentor the youth to become the best versions of themselves.</p>
  <a class="btn" style="left:75px;top:1211px;width:202px;height:59px;color:var(--white)">Read More</a>
  <div class="abs about-frame"></div>
  <div class="abs about-photo" role="img" aria-label="Batter swinging at home plate with catcher crouched behind"></div>
</section>

<section>
  <div class="abs facility-bg" role="img" aria-label="Dimmed crowd of players and spectators at a ballpark"></div>
  <h2 class="abs section-title-light">OUR FACILITY</h2>
  <div class="abs card" style="left:75px">
    <div class="card-photo" role="img" aria-label="Softball batter making contact with a pitch on a dirt infield" style="background:linear-gradient(135deg,#8c7a60,#c6a27c 50%,#a07a5a)"></div>
    <h3>BASEBALL TRAINING</h3>
    <p>Sed ut perspiciatis unde omnis iste natus error sit voluptatem accusantium doloremque laudantium sint occaecat cupidatat no.</p>
  </div>
  <a class="btn" style="left:238px;top:2094px;width:203px;height:59px">Read More</a>
  <div class="abs card" style="left:615px">
    <div class="card-photo" role="img" aria-label="Softball team posing together on a field in front of batting cages" style="background:linear-gradient(180deg,#9aa0a6,#5b5e62 50%,#5e7448)"></div>
    <h3>SOFTBALL INDOOR TRAINING</h3>
    <p>Sed ut perspiciatis unde omnis iste natus error sit voluptatem accusantium doloremque laudantium sint occaecat cupidatat no.</p>
  </div>
  <a class="btn" style="left:770px;top:2094px;width:203px;height:59px">Read More</a>
</section>

<section>
  <div class="abs lessons-dark" role="img" aria-label="Team celebrating with medals and a championship banner"></div>
  <svg class="abs" style="left:0;top:2234px" width="1200" height="479"><polygon points="635,0 1200,0 1200,479 575,479" fill="var(--green-deep)" opacity=".92"/></svg>
  <p class="abs lesson-l">Baseball/Softball<br>Hitting Lessons<br><span class="price">$55/30 mins</span></p>
  <a class="btn" style="left:75px;top:2523px;width:202px;height:59px">Read More</a>
  <p class="abs lesson-r">Baseball/<br>Softball Fielding/<br>Throwing Lessons<br>$55/30 mins</p>
  <a class="btn" style="left:922px;top:2546px;width:203px;height:59px">Read More</a>
  <div class="abs lessons-circle">LESSONS<br>PRICING</div>
</section>

<section>
  <h2 class="abs camps-title">CAMPS &amp; CLASSES</h2>
  <div class="abs camp" style="left:75px;background:linear-gradient(135deg,#2f2f33,#5a6a4a)" role="img" aria-label="Players practicing hitting inside indoor batting cages"></div>
  <div class="abs camp" style="left:432px;background:linear-gradient(180deg,#7a8fa8,#b23838 55%,#6d6a66)" role="img" aria-label="Softball team in red uniforms posing in two rows"></div>
  <div class="abs camp" style="left:789px;background:linear-gradient(180deg,#8a8c90,#a8303a 55%,#3a3e55)" role="img" aria-label="Champion team in red holding a banner with coaches"></div>
  <svg class="abs" style="left:0;top:3116px" width="1200" height="81"><polygon points="605,80 1200,0 1200,80" fill="var(--green)"/></svg>
</section>

<footer class="site-footer">
  <div class="abs footer-bg"></div>
  <div class="brand"><span class="dot"></span><span>Timber Ridge Athletics</span></div>
  <p class="abs copy">©2022 by CompanyName.<br>All Right Reserved</p>
  <span class="abs social" style="left:75px"></span>
  <span class="abs social" style="left:131px"></span>
  <span class="abs social" style="left:187px"></span>
  <span class="abs social" style="left:245px"></span>

  <h4 class="abs foot-h" style="left:355px">SITE MAP</h4>
  <ul class="abs sitemap">
    <li>Home</li><li>About Us</li><li>Our Facility</li><li>Lessons</li><li>Team Rental Pricing</li><li>Instructor Opprtotunities</li><li>Camps/Classes</li><li>More</li>
  </ul>

  <h4 class="abs foot-h" style="left:596px">CONTACT INFO</h4>
  <div class="abs contact-row" style="top:3308px">
    <svg width="18" height="14" viewBox="0 0 18 14"><path d="M1 2l5-2 6 2 5-2v12l-5 2-6-2-5 2z" fill="var(--green)"/></svg>
    <span>2870 Larkspur Way Suite #210<br>Maple Hollow,<br>Ca 95000</span>
  </div>
  <div class="abs contact-row" style="top:3394px">
    <svg width="18" height="16" viewBox="0 0 24 24"><path d="M6.6 10.8a15 15 0 006.6 6.6l2.2-2.2a1 1 0 011-.25 11 11 0 003.5.56 1 1 0 011 1V20a1 1 0 01-1 1A17 17 0 013 4a1 1 0 011-1h3.5a1 1 0 011 1 11 11 0 00.56 3.5 1 1 0 01-.25 1z" fill="var(--green)"/></svg>
    <span>555-014-2386</span>
  </div>
  <div class="abs contact-row" style="top:3436px">
    <svg width="18" height="14" viewBox="0 0 18 14"><rect width="18" height="14" rx="2" fill="var(--green)"/><path d="M1 1l8 6 8-6" stroke="var(--footer)" stroke-width="1.6" fill="none"/></svg>
    <span>info@companyname.com</span>
  </div>

  <h4 class="abs foot-h" style="left:901px">HOURS</h4>
  <div class="abs hours">
    <div><span>Mon-Thu</span><span>3:00-9:00:pm</span></div>
    <div><span>Fri</span><span>4:00pm-7:00pm</span></div>
    <div><span>Sat</span><span>Closed</span></div>
    <div><span>Sun</span><span>Closed</span></div>
  </div>
</footer>

</body>
</html>
```